NZ First of it's kind solutions directory and marketplace for busy Mums needs a business card design

We need a business card design for our new nationwide business in NZ (long term plans to go global). We provide solutions to the everyday challenges that busy Mums face by connecting them with quality communities and suppliers of carefully selected, relevant products and services. We sell direct via our online marketplace. The final design should communicate our values of inclusivity, quality and smart solutions. Colours should incorporate our logo colour palette of #477077 and #6ba8b2. Our website is at https://www.brightnestmums.example

Target Market(s)

busy Mums, Age 28 – 50, female, income over $100K, location main centres NZ primarily but NZ wide. Is likely juggling work or career with a young family. Probably had hobbies which have fallen by the wayside.
-Wants to succeed in her chosen career without compromising on family life
-to successfully juggle her career without feeling like she is compromising her children
- Is time poor, something always has to give and it’s generally her health (she’ll stay up late, get stressed)
- probably ex corporate or professional career. Has discretional income

Industry/Entity Type

Business

Contact Information for Business Card

Lena Forbisher, Founder, BrightNestMums.example (Strapline Tap; Gather; Sorted), 47 Kowhai Terrace, Ellerslie, Auckland 1051, New Zealand. Mob: 021 483 517 Ph: +64 (0)9 571 4860

Font styles to use
Other font styles liked:
• Raleway, and/or Architects Daughter

Colors
00a990
33b8a4
86cfc6
cfeae6

Requirements
Must have
• the above details, streamline. the logo and colours associated with those logos
Should not have
• foil or metallic colours

```html
<!DOCTYPE html>
<html lang="en">
<head>
<meta charset="utf-8">
<title>BrightNestMums – Business Card</title>
<link rel="stylesheet" href="https://fonts.googleapis.com/css2?family=Nunito:ital,wght@0,700;0,800;1,400&family=Roboto:ital,wght@0,400;1,400&display=swap">
<style>
  :root {
    --canvas-bg: #e4e1dd;
    --card-bg: #f5f2ee;
    --brand-dark: #477077;
    --brand-light: #6ba8b2;
    --band-dark: #2f5359;
    --ink: #3e4a4c;
    --ink-soft: #5a6567;
    --web-text: #e3d8c2;
  }
  * { margin: 0; padding: 0; box-sizing: border-box; }
  html, body {
    width: 1200px; height: 1047px; overflow: hidden;
    background: var(--canvas-bg);
  }
  .business-card {
    position: absolute; left: 100px; top: 224px;
    width: 1000px; height: 598px;
    background: var(--card-bg);
    border-radius: 4px;
    box-shadow: 0 6px 24px rgba(0,0,0,0.12);
    overflow: hidden;
    font-family: "Roboto", Arial, sans-serif;
  }
  .brand-block {
    position: absolute; left: 40px; top: 130px; width: 470px;
    text-align: center;
  }
  .brand-dot {
    width: 96px; height: 96px; border-radius: 50%;
    background: var(--brand-dark);
    margin: 0 auto 40px;
  }
  .brand-name {
    font-family: "Nunito", Arial, sans-serif;
    font-weight: 800; font-size: 48px; line-height: 1;
    color: var(--brand-dark); letter-spacing: -0.5px;
  }
  .brand-strapline {
    margin-top: 16px;
    font-size: 17px; letter-spacing: 6px;
    color: var(--ink-soft);
  }
  .brand-strapline .divider { color: var(--brand-light); padding: 0 6px; }
  .contact-block { position: absolute; left: 558px; top: 112px; }
  .contact-name {
    font-family: "Nunito", Arial, sans-serif;
    font-weight: 800; font-size: 36px; line-height: 1;
    color: var(--brand-dark);
  }
  .contact-role {
    margin-top: 10px;
    font-style: italic; font-size: 22px; color: var(--ink);
  }
  .contact-address {
    margin-top: 36px; font-size: 22px; line-height: 36px; color: var(--ink);
  }
  .contact-list { margin-top: 22px; list-style: none; }
  .contact-list li {
    display: flex; align-items: center;
    font-size: 22px; line-height: 38px; color: var(--ink);
  }
  .contact-icon { width: 20px; height: 20px; margin-right: 18px; flex: none; }
  .footer-band { position: absolute; left: 0; bottom: 0; width: 1000px; height: 76px; }
  .footer-web {
    position: absolute; left: 558px; bottom: 22px;
    font-size: 22px; color: var(--web-text);
  }
</style>
</head>
<body>
  <div class="business-card">
    <div class="brand-block">
      <div class="brand-dot"></div>
      <div class="brand-name">BrightNestMums</div>
      <div class="brand-strapline">TAP<span class="divider">|</span>GATHER<span class="divider">|</span>SORTED</div>
    </div>

    <div class="contact-block">
      <div class="contact-name">Lena Forbisher</div>
      <div class="contact-role">Founder</div>
      <div class="contact-address">47 Kowhai Terrace, Ellerslie,<br>Auckland 1051, New Zealand</div>
      <ul class="contact-list">
        <li>
          <svg class="contact-icon" viewBox="0 0 20 20" aria-hidden="true">
            <rect x="5" y="1" width="10" height="18" rx="2" fill="var(--brand-dark)"/>
            <rect x="7" y="4" width="6" height="10" fill="var(--card-bg)"/>
          </svg>
          021 483 517
        </li>
        <li>
          <svg class="contact-icon" viewBox="0 0 20 20" aria-hidden="true">
            <path d="M2 7c0-3 4-4 8-4s8 1 8 4v1h-4V6H6v2H2z" fill="var(--brand-dark)"/>
            <path d="M5 9h10l2 8H3z" fill="var(--brand-dark)"/>
            <circle cx="10" cy="13" r="2" fill="var(--card-bg)"/>
          </svg>
          +64 (0)9 571 4860
        </li>
        <li>
          <svg class="contact-icon" viewBox="0 0 20 20" aria-hidden="true">
            <rect x="1" y="4" width="18" height="12" fill="var(--brand-dark)"/>
            <path d="M1 4l9 7 9-7" fill="none" stroke="var(--card-bg)" stroke-width="1.6"/>
          </svg>
          lena@brightnestmums.example
        </li>
      </ul>
    </div>

    <svg class="footer-band" viewBox="0 0 1000 76" aria-hidden="true">
      <rect x="0" y="52" width="520" height="24" fill="var(--brand-dark)"/>
      <path d="M510 0 H1000 V76 H455 C470 40 480 0 510 0 Z" fill="var(--band-dark)"/>
    </svg>
    <div class="footer-web">www.BrightNestMums.example</div>
  </div>
</body>
</html>
```